Stylish Business Cards Wanted

- DOUBLE SIDED Design Required -

High end, edgy cards for a corporate and personal stylist. Must include logo,
Name: Belinda Harwick
Title: Director and Stylist
telephone : +61 8 7142 5809
email: belinda@theloombriefing.example
website: theloombriefing.example
Tag: Corporate Workwear & Uniform Specialist | Personal Stylist
Would like nice icons for telephone, email, website

Target Market(s)

Businesses wanting stylish uniforms, people wanting stylish wardrobes

Industry/Entity Type

Corporate Workwear Stylist

Contact Information for Business Card

I would like black, white and gold foiling incorporated in the design - possibly a touch of the other colours on my branding guide attached Name: Belinda Harwick Title: Director and Stylist telephone : +61 8 7142 5809 email: belinda@theloombriefing.example website: theloombriefing.example Tag: Corporate Workwear & Uniform Specialist | Personal Stylist Would like nice icons for telephone, email, website

Font styles to use
Other font styles liked:
• Raleway

Colors

Designer to choose colors to be used in the design.

Requirements
Must have
• Gold foil accents

```html
<!DOCTYPE html>
<html lang="en">
<head>
<meta charset="utf-8">
<title>The Loom Briefing – Business Cards</title>
<link rel="stylesheet" href="https://fonts.googleapis.com/css2?family=Montserrat:wght@400;500;600&family=Raleway:wght@400;500&display=swap">
<style>
  :root {
    --stage: #dcdcdc;
    --ink: #0b0b0b;
    --card-white: #ffffff;
    --gold: #e2b53e;
    --gold-deep: #c99a22;
    --pattern-dark: #111314;
    --pattern-mid: #1d2223;
  }
  * { box-sizing: border-box; margin: 0; padding: 0; }
  html, body { width: 1200px; height: 900px; overflow: hidden; }
  body {
    background: var(--stage);
    font-family: "Montserrat", sans-serif;
    position: relative;
  }
  .card {
    position: absolute;
    left: 250px;
    width: 700px;
    height: 400px;
    overflow: hidden;
    box-shadow: 0 6px 18px rgba(0,0,0,0.22);
  }

  /* Back side */
  .card--back { top: 40px; background: var(--ink); }
  .back-pattern {
    position: absolute; inset: 0;
    background: linear-gradient(120deg, var(--pattern-dark) 0%, var(--pattern-mid) 55%, var(--pattern-dark) 100%);
  }
  .back-wordmark {
    position: absolute;
    left: 455px; top: 300px;
    font-weight: 600;
    font-size: 22px;
    color: var(--gold);
    letter-spacing: 0.5px;
  }

  /* Front side */
  .card--front { top: 470px; background: var(--card-white); }
  .front-wordmark {
    position: absolute;
    top: 70px; left: 0; right: 0;
    text-align: center;
    font-weight: 600;
    font-size: 44px;
    color: var(--ink);
    letter-spacing: 1px;
  }
  .holder {
    position: absolute;
    right: 390px; top: 205px;
    text-align: right;
  }
  .holder-name {
    font-weight: 500;
    font-size: 26px;
    color: var(--gold);
    letter-spacing: 1px;
    line-height: 1;
  }
  .holder-title {
    font-family: "Raleway", sans-serif;
    font-size: 14px;
    color: var(--ink);
    margin-top: 3px;
  }
  .divider {
    position: absolute;
    left: 349px; top: 170px;
    width: 2px; height: 110px;
    background: var(--gold);
  }
  .contact-icons {
    position: absolute;
    left: 380px; top: 150px;
    display: flex; gap: 16px;
  }
  .contact-icons svg { width: 22px; height: 22px; display: block; }
  .contact-list {
    position: absolute;
    left: 380px; top: 185px;
    list-style: none;
    font-family: "Raleway", sans-serif;
    font-size: 15px;
    line-height: 24px;
    color: var(--ink);
  }
  .tag-band {
    position: absolute;
    left: 0; right: 0; top: 318px;
    height: 46px;
    background: var(--ink);
    border-top: 3px solid var(--gold);
    border-bottom: 3px solid var(--gold);
    outline: 4px solid var(--card-white);
    display: flex; align-items: center; justify-content: center;
    gap: 14px;
    font-weight: 500;
    font-size: 17px;
    letter-spacing: 0.5px;
    color: var(--gold);
    text-transform: uppercase;
  }
  .tag-band .sep { color: var(--card-white); }
  .gold-rule-top {
    position: absolute; left: 0; right: 0; top: 308px;
    height: 3px; background: var(--gold);
  }
  .gold-edge {
    position: absolute; left: 0; right: 0; bottom: 0;
    height: 8px; background: var(--gold);
    border-top: 6px solid var(--card-white);
  }
</style>
</head>
<body>

<section class="card card--back" aria-label="Business card back">
  <div class="back-pattern" role="img" aria-label="Repeating tone-on-tone brand wordmark pattern"></div>
  <div class="back-wordmark">The Loom Briefing</div>
</section>

<section class="card card--front" aria-label="Business card front">
  <div class="front-wordmark">The Loom Briefing</div>

  <div class="holder">
    <div class="holder-name">Belinda Harwick</div>
    <div class="holder-title">Director and Stylist</div>
  </div>

  <div class="divider"></div>

  <div class="contact-icons">
    <svg viewBox="0 0 24 24" aria-label="Telephone">
      <circle cx="12" cy="12" r="12" fill="var(--ink)"/>
      <path d="M8.3 6.5l1.9-.4 1.1 2.6-1.3 1c.6 1.4 1.6 2.4 3 3l1-1.3 2.6 1.1-.4 1.9c-.1.4-.5.7-.9.7C10.6 15 9 13.4 7.6 7.4c0-.4.3-.8.7-.9z" fill="var(--gold)"/>
    </svg>
    <svg viewBox="0 0 24 24" aria-label="Email">
      <circle cx="12" cy="12" r="12" fill="var(--ink)"/>
      <rect x="6.5" y="8" width="11" height="8" fill="var(--gold)"/>
      <path d="M6.5 8l5.5 4.5L17.5 8" fill="none" stroke="var(--ink)" stroke-width="1"/>
    </svg>
    <svg viewBox="0 0 24 24" aria-label="Website">
      <circle cx="12" cy="12" r="12" fill="var(--ink)"/>
      <circle cx="12" cy="12" r="5.5" fill="none" stroke="var(--gold)" stroke-width="1.3"/>
      <ellipse cx="12" cy="12" rx="2.3" ry="5.5" fill="none" stroke="var(--gold)" stroke-width="1.1"/>
      <path d="M6.5 12h11" stroke="var(--gold)" stroke-width="1.1"/>
    </svg>
  </div>

  <ul class="contact-list">
    <li>+61 8 7142 5809</li>
    <li>belinda@theloombriefing.example</li>
    <li>theloombriefing.example</li>
  </ul>

  <div class="gold-rule-top"></div>
  <div class="tag-band">
    <span>Corporate Workwear</span><span class="sep">|</span>
    <span>Uniform Specialist</span><span class="sep">|</span>
    <span>Personal Stylist</span>
  </div>
  <div class="gold-edge"></div>
</section>

</body>
</html>
```